Business Card Design for a Software Startup

We'd like to have a business card design. We already have a logo. Basically what we need is a clean design with name, address, cellphone and phone numbers, e-mail and web site address (front) and a space on the back with our logo with the company name on the right side and some texts on the bottom.
We are a development and consulting company in Brazil with highly qualified team of professionals in Java, iOS and Android development and consulting.

Target Market(s)

CIO, IT managers of mid to big size companies

Industry/Entity Type

Business

```html
<!DOCTYPE html>
<html lang="en">
<head>
<meta charset="utf-8">
<title>Vantrel Business Cards</title>
<link rel="stylesheet" href="https://fonts.googleapis.com/css2?family=Arimo:wght@400;700&display=swap">
<style>
  :root {
    --page-bg: #e9e7e3;
    --card-white: #ffffff;
    --navy: #213b7a;
    --royal: #2b3a86;
    --sky: #0b9ad6;
    --cyan-line: #1b8fd0;
    --brand-ink: #14376f;
    --grey-text: #6b6b6b;
    --white: #ffffff;
  }
  * { margin: 0; padding: 0; box-sizing: border-box; }
  html, body { width: 1200px; height: 720px; overflow: hidden; }
  body {
    background: var(--page-bg);
    font-family: "Arimo", Arial, sans-serif;
    position: relative;
  }
  .card {
    position: absolute;
    top: 205px;
    width: 540px;
    height: 309px;
    border-radius: 4px;
    overflow: hidden;
    box-shadow: 0 6px 18px rgba(0,0,0,0.18);
  }
  /* ---------- Front ---------- */
  .card-front { left: 40px; background: var(--card-white); }
  .brand {
    position: absolute;
    left: 42px;
    top: 38px;
    display: flex;
    align-items: center;
    gap: 16px;
  }
  .brand-square {
    width: 62px;
    height: 62px;
    border-radius: 10px;
    background: var(--navy);
  }
  .brand-name {
    font-weight: 700;
    font-size: 60px;
    letter-spacing: 2px;
    color: var(--brand-ink);
    line-height: 1;
  }
  .address {
    position: absolute;
    left: 62px;
    top: 122px;
    font-size: 13px;
    letter-spacing: 1.6px;
    color: var(--grey-text);
    white-space: nowrap;
  }
  .band { position: absolute; left: 0; top: 0; width: 540px; height: 309px; }
  .holder {
    position: absolute;
    left: 170px;
    top: 242px;
    width: 160px;
    text-align: right;
    color: var(--white);
  }
  .holder-name { font-weight: 700; font-size: 20px; line-height: 22px; }
  .holder-title { font-size: 12px; margin-top: 2px; }
  .divider {
    position: absolute;
    left: 343px;
    top: 216px;
    width: 1px;
    height: 66px;
    background: rgba(255,255,255,0.7);
  }
  .contacts {
    position: absolute;
    left: 356px;
    top: 212px;
    list-style: none;
    color: var(--white);
    font-size: 12.5px;
    letter-spacing: 0.5px;
    line-height: 18px;
  }
  /* ---------- Back ---------- */
  .card-back {
    left: 620px;
    background: radial-gradient(ellipse 55% 70% at 50% 45%, var(--sky) 0%, #1573b5 35%, var(--royal) 80%);
  }
  .back-brand {
    position: absolute;
    left: 0; right: 0;
    top: 96px;
    display: flex;
    justify-content: center;
    align-items: center;
    gap: 16px;
  }
  .back-square {
    width: 74px;
    height: 74px;
    border-radius: 12px;
    background: var(--white);
  }
  .back-name {
    font-weight: 700;
    font-size: 52px;
    letter-spacing: 2px;
    color: var(--white);
  }
  .back-web {
    position: absolute;
    left: 0; right: 0;
    bottom: 40px;
    text-align: center;
    color: var(--white);
    font-weight: 700;
    font-size: 17px;
    letter-spacing: 5px;
  }
</style>
</head>
<body>
  <section class="card card-front" aria-label="Business card front">
    <div class="brand">
      <span class="brand-square"></span>
      <span class="brand-name">VANTREL</span>
    </div>
    <p class="address">Door No. Street Name City Name, State, Zip Code.</p>
    <svg class="band" viewBox="0 0 540 309" aria-hidden="true">
      <defs>
        <linearGradient id="bandFill" x1="0" y1="0" x2="1" y2="0">
          <stop offset="0" stop-color="#1c3a78"/>
          <stop offset="1" stop-color="#17306a"/>
        </linearGradient>
      </defs>
      <path d="M0 262 C 180 262, 360 215, 540 120 L540 309 L0 309 Z" fill="url(#bandFill)"/>
      <path d="M0 252 C 180 252, 360 205, 540 110" fill="none" stroke="var(--cyan-line)" stroke-width="3"/>
    </svg>
    <div class="holder">
      <div class="holder-name">Your Name</div>
      <div class="holder-title">Title</div>
    </div>
    <span class="divider"></span>
    <ul class="contacts">
      <li>p: 123-456-7890</li>
      <li>c: 123-456-7890</li>
      <li>e: yourname@vantrel.com</li>
      <li>w: www.vantrel.com</li>
    </ul>
  </section>

  <section class="card card-back" aria-label="Business card back">
    <div class="back-brand">
      <span class="back-square"></span>
      <span class="back-name">VANTREL</span>
    </div>
    <p class="back-web">www.vantrel.com</p>
  </section>
</body>
</html>
```